Heron Dusk business card design

I make handmade colourful women's beaded jewellery (necklaces and earnings).
I require a business card to be designed to truly reflect my jewellery, that is, it is different and stands out.
I would like the business card to look creative, arty, gentle and feminine and fit in with the look of my website and logo (already developed).
I would like the business card to have strong use of the water reeds that are flowing in the wind (please see the banner image on my website www.herondusk.net and attached files).

Target Market(s)

Women who are fashion conscious, hip and funky. My audience like things that are a little different and stand out in a crowd.These women are aged in their 20's-40's.

Industry/Entity Type

Jewelry

Contact Information for Business Card

Please include the following items:
1) my logo: Heron Dusk
2) my name, address and phone number: Darla Fontenot, Sydney, Australia, 0498 315 270
3) my web details: www.herondusk.net, info@herondusk.net, www.facebook.com/herondusk

Font styles to use
Other font styles liked:
• Remachine Script

Requirements
Must have
• My business card must have the following:
• 1) my personal details including all my website contacts (see above).
• 2) Heron Dusk logo
• 3) Reeds flowing in the wind (see my banner image on my website www.herondusk.net or see attached files).
Nice to have
• A sunrise in the background (rising over water)
• I would prefer that the colour scheme to fit with the Heron Dusk logo, that is the colours of an early morning sunrise i.e yellows, oranges. The use of black and white is fine.
Should not have
• I do not like a commercial manufactured look with hard edges. I would like a look that is soft and reflects an artistic, creative and independent business.

```html
<!DOCTYPE html>
<html lang="en">
<head>
<meta charset="utf-8">
<title>Heron Dusk – Business Card</title>
<link href="https://fonts.googleapis.com/css2?family=Arimo:wght@400;700&display=swap" rel="stylesheet">
<style>
  :root{
    --bg:#ece8e2;
    --card:#ffffff;
    --ink:#1f1f1f;
    --ink-soft:#3a3a3a;
    --rule:#9a9a9a;
    --sun-light:#fcd21c;
    --sun-deep:#f2a900;
    --sun-dusk:#e08a00;
    --sun-edge:#232323;
    --dot:#555555;
  }
  *{box-sizing:border-box;margin:0;padding:0}
  html,body{width:1200px;height:950px;overflow:hidden;background:var(--bg);font-family:"Arimo",Arial,sans-serif}
  .sheet{position:relative;width:1200px;height:950px}
  .card{position:absolute;left:230px;width:740px;height:423px;background:var(--card);border-radius:26px;overflow:hidden;box-shadow:0 6px 18px rgba(0,0,0,.18)}
  .card--front{top:32px}
  .card--back{top:495px}

  /* front */
  .logo{position:absolute;left:0;right:0;top:62px;display:flex;flex-direction:column;align-items:center}
  .logo__name{font-size:34px;font-weight:400;color:var(--ink);letter-spacing:.5px;line-height:1}
  .logo__disc{margin-top:12px;width:160px;height:160px;border-radius:50%;border:3px solid var(--sun-edge);
    background:
      radial-gradient(ellipse 70% 40% at 50% 95%,rgba(90,50,0,.55),transparent 70%),
      radial-gradient(circle at 50% 38%,var(--sun-light),var(--sun-deep) 60%,var(--sun-dusk))}
  .social-rule{position:absolute;left:110px;right:110px;top:338px;height:1px;background:linear-gradient(90deg,transparent,var(--rule) 20%,var(--rule) 80%,transparent)}
  .social{position:absolute;left:0;right:0;top:326px;display:flex;justify-content:center;gap:8px}
  .social__dot{width:24px;height:24px;border-radius:50%;background:var(--dot);border:2px solid var(--card)}

  /* back */
  .sun{position:absolute;left:0;top:0}
  .reeds{position:absolute;left:150px;top:175px;width:250px;height:248px;border-radius:50% 50% 0 0;
    background:radial-gradient(ellipse 60% 70% at 50% 100%,rgba(150,90,0,.28),rgba(150,90,0,.08) 60%,transparent 75%)}
  .brand{position:absolute;right:62px;top:74px;font-size:60px;font-weight:400;color:var(--ink);line-height:1}
  .brand span{display:block}
  .brand span + span{margin-left:70px;margin-top:4px}
  .contact{position:absolute;left:62px;top:232px;color:var(--ink-soft);font-size:16px;line-height:20px}
  .contact__name{font-size:23px;font-weight:700;color:var(--ink);line-height:26px}
  .contact__role{margin-bottom:4px}
  .contact__row{display:flex;align-items:center;gap:9px}
  .contact__row svg{width:14px;height:14px;flex:none}
</style>
</head>
<body>
<main class="sheet">

  <section class="card card--front" aria-label="Card front">
    <div class="logo">
      <div class="logo__name">Heron Dusk</div>
      <div class="logo__disc" role="img" aria-label="Round sunrise emblem with heron silhouette and water reeds flowing in the wind"></div>
    </div>
    <div class="social-rule"></div>
    <div class="social" aria-label="Social links">
      <span class="social__dot"></span><span class="social__dot"></span><span class="social__dot"></span><span class="social__dot"></span>
    </div>
  </section>

  <section class="card card--back" aria-label="Card back">
    <svg class="sun" width="740" height="423" viewBox="0 0 740 423" aria-hidden="true">
      <defs>
        <linearGradient id="sunFill" x1="0" y1="0" x2="0" y2="1">
          <stop offset="0" stop-color="#fcd21c"/>
          <stop offset="1" stop-color="#f2a900"/>
        </linearGradient>
      </defs>
      <circle cx="170" cy="470" r="344" fill="#232323"/>
      <circle cx="170" cy="470" r="336" fill="url(#sunFill)"/>
    </svg>
    <div class="reeds" role="img" aria-label="Faint heron and water reeds flowing in the wind over the rising sun"></div>

    <div class="brand"><span>Heron</span><span>Dusk</span></div>

    <div class="contact">
      <div class="contact__name">Jon Doran</div>
      <div class="contact__role">President</div>
      <div>Darla Fontenot</div>
      <div>Sydney, Australia</div>
      <div class="contact__row">
        <svg viewBox="0 0 16 16"><path fill="#1f1f1f" d="M2 5c0-1.5 2-3 6-3s6 1.5 6 3v1h-3V5H5v1H2z M4 7h8l2 6H2z"/><circle cx="8" cy="10" r="1.6" fill="#f9c20a"/></svg>
        <span>0498 315 270</span>
      </div>
      <div class="contact__row">
        <svg viewBox="0 0 16 16"><rect x="1" y="3" width="14" height="10" rx="1" fill="#1f1f1f"/><path d="M1.5 4 8 9l6.5-5" fill="none" stroke="#f9c20a" stroke-width="1.4"/></svg>
        <span>info@herondusk.net</span>
      </div>
      <div class="contact__row">
        <svg viewBox="0 0 16 16"><circle cx="8" cy="8" r="7" fill="#1f1f1f"/><path d="M1 8h14M8 1c-3 3-3 11 0 14M8 1c3 3 3 11 0 14" fill="none" stroke="#f9c20a" stroke-width="1"/></svg>
        <span>www.herondusk.net</span>
      </div>
      <div class="contact__row">
        <svg viewBox="0 0 16 16"><rect x="1" y="1" width="14" height="14" rx="2" fill="#1f1f1f"/></svg>
        <span>herondusk</span>
      </div>
    </div>
  </section>

</main>
</body>
</html>
```